Album Cover for Tunevale/Orchard Sound Neoclassical

I would like to get a new album cover design for a new release called 'Veldarine' by Tom Harwick. <br/>Some creative pointers - <br/>The meaning of veldarine is "the desire to care less about things..." to be a child again to be totally free. <br/>It is an album of upright piano solo pieces so perhaps some hint of an old retro upright piano as well as a sense of freedom. <br/>I like bright colour but equally I also like simple black & white.<br/>I am a fan of Lena Sorbeck and Pavel Ostrani so perhaps look at some of their covers as a guide. <br/>

Target Market(s)

20-40 yr old m&f - fans of Tobias Vennmark or Lena Sorbeck

Font styles to use
Serif

Colors

Designer to choose colors to be used in the design.

Requirements
Must have
• a sense of piano classical but more cinematic than formal/traditional classical
• Also a sense of freedom as above
Nice to have
• something modern looking as if it were a pop track but for classical
Should not have
• nothing too dark grey, dark green, dark sombre feel

```html
<!DOCTYPE html>
<html lang="en">
<head>
<meta charset="utf-8">
<title>Veldarine – Tom Harwick</title>
<link href="https://fonts.googleapis.com/css2?family=Open+Sans:wght@800&family=Raleway:wght@300&display=swap" rel="stylesheet">
<style>
  :root {
    --stage: #dcdcdc;
    --night: #040d14;
    --night-mid: #0a1822;
    --smoke: #4f6475;
    --smoke-soft: #2c3e4c;
    --key-ivory: #e6e7ea;
    --key-ebony: #2a2626;
    --ink: #ffffff;
    --frame: #ffffff;
  }
  html, body {
    margin: 0;
    padding: 0;
    width: 1200px;
    height: 1026px;
    overflow: hidden;
    background: var(--stage);
  }
  .album-cover {
    position: absolute;
    left: 130px;
    top: 43px;
    width: 940px;
    height: 940px;
    overflow: hidden;
    background: var(--night);
    box-shadow: 8px 8px 10px rgba(0,0,0,0.25);
  }
  .smoke-backdrop {
    position: absolute;
    inset: 0;
    background:
      radial-gradient(ellipse 55% 30% at 55% 102%, var(--smoke) 0%, rgba(79,100,117,0) 100%),
      radial-gradient(ellipse 45% 25% at 95% 92%, var(--smoke-soft) 0%, rgba(44,62,76,0) 100%),
      radial-gradient(ellipse 50% 22% at 40% 78%, var(--smoke-soft) 0%, rgba(44,62,76,0) 100%),
      linear-gradient(180deg, var(--night) 0%, var(--night) 45%, var(--night-mid) 70%, var(--smoke-soft) 100%);
  }
  .piano-keys {
    position: absolute;
    left: 0;
    top: 0;
    width: 940px;
    height: 290px;
    background: linear-gradient(180deg, var(--key-ebony) 0%, #6e6c6e 45%, var(--key-ivory) 62%, var(--key-ivory) 100%);
  }
  .cover-frame {
    position: absolute;
    left: 24px;
    top: 264px;
    width: 887px;
    height: 650px;
    border: 3px solid var(--frame);
    border-top: none;
  }
  .album-title {
    position: absolute;
    left: 0;
    top: 450px;
    width: 940px;
    margin: 0;
    text-align: center;
    font-family: "Open Sans", sans-serif;
    font-weight: 800;
    font-size: 152px;
    line-height: 1;
    letter-spacing: -4px;
    color: var(--ink);
  }
  .artist-name {
    position: absolute;
    left: 0;
    top: 740px;
    width: 940px;
    margin: 0;
    text-align: center;
    font-family: "Raleway", sans-serif;
    font-weight: 300;
    font-size: 64px;
    line-height: 1;
    letter-spacing: 0.2em;
    text-indent: 0.2em;
    color: var(--ink);
  }
</style>
</head>
<body>
  <section class="album-cover">
    <div class="smoke-backdrop" role="img" aria-label="Dark blue smoke drifting up from the bottom of the cover"></div>
    <div class="piano-keys" role="img" aria-label="Row of black and white piano keys hanging down from the top edge at uneven lengths"></div>
    <div class="cover-frame"></div>
    <h1 class="album-title">VELDARINE</h1>
    <p class="artist-name">TOM HARWICK</p>
  </section>
</body>
</html>
```